OrvanoGoodsHub.com -Ecommerce Website for Luxury Products

This will be an ecommerce site. A website portal that will allow both consumers to enter one way and see specific purchase options and businesses to enter via a different link that allows B2B to see their specific options once logged into. B2C can purchase both as a guest/or after account is setup. B2B must be approved to set up account. This is front end website project. Back-end integration is separate. Will be hosted on Servantia with a domain registration held at Pexadrinet. Additional website concept/idea/synergy can be found from sister site-KRWZHospitality.com

```html
<!DOCTYPE html>
<html lang="en">
<head>
<meta charset="utf-8">
<title>Orvano Goods — Purveyors of Luxury Lifestyle Accoutrements</title>
<link href="https://fonts.googleapis.com/css2?family=Cinzel:wght@500;600&family=Inter:wght@400;500;600;700&display=swap" rel="stylesheet">
<style>
:root{
  --black:#000;
  --ink:#0c0b0a;
  --panel:#141210;
  --dark-brown:#1d1915;
  --brown:#6f5d4e;
  --brown-line:#7a6553;
  --frame:#8a7462;
  --white:#fff;
  --muted:#d9d4cf;
  --star:#f5b400;
}
*{box-sizing:border-box;margin:0;padding:0}
html,body{width:1200px;height:3686px;overflow:hidden;background:var(--black)}
body{font-family:"Inter",sans-serif;color:var(--white);position:relative}
.serif{font-family:"Cinzel",serif}
section,header,footer{position:absolute;left:0;width:1200px}
.abs{position:absolute}
.btn{position:absolute;background:var(--brown);color:var(--white);border-radius:22px;font-weight:600;font-size:14px;display:flex;align-items:center;justify-content:center}
.heading{font-family:"Cinzel",serif;font-weight:500;font-size:36px;letter-spacing:.5px;text-transform:uppercase}
.rule{height:2px;width:62px;background:var(--brown-line);position:absolute}
.body-copy{font-size:13.5px;line-height:24px;text-align:justify;color:var(--muted)}
.circle-btn{position:absolute;width:36px;height:36px;border-radius:50%;background:var(--white);display:flex;align-items:center;justify-content:center}

/* nav */
.nav{top:0;height:57px;background:rgba(0,0,0,.85);z-index:3}
.nav a{position:absolute;top:0;height:57px;line-height:57px;font-size:15px;color:var(--white);text-decoration:none}
.nav .active{background:var(--brown);padding:0 16px;height:40px;line-height:40px;top:16px}
.brand{position:absolute;left:510px;top:14px;width:180px;text-align:center}
.brand-name{font-family:"Cinzel",serif;font-size:17px;font-weight:500;letter-spacing:.5px}
.brand-sub{font-family:"Cinzel",serif;font-size:6.5px;font-weight:500;letter-spacing:1px;margin-top:2px}
.brand-tag{font-family:"Cinzel",serif;font-size:6.5px;font-weight:500;margin-top:4px}

/* hero */
.hero{top:0;height:638px;background:radial-gradient(ellipse at 60% 30%,#3a3028 0%,#1e1915 45%,#0d0b09 100%)}
.hero-title{position:absolute;top:240px;width:100%;text-align:center;font-family:"Cinzel",serif;font-weight:500;font-size:46px;line-height:58px}
.hero-sub{position:absolute;top:358px;width:100%;text-align:center;font-size:30px}

/* story */
.story{top:638px;height:585px;background:var(--black)}
.photo{position:absolute;border:2px solid var(--frame);padding:8px}
.photo .fill{width:100%;height:100%}

/* featured */
.featured{top:1223px;height:647px;background:linear-gradient(180deg,#1f1b17,#2a241f 50%,#1b1714)}
.card{position:absolute;top:157px;width:284px;height:387px;background:var(--black);text-align:center}
.card h3{font-size:17px;font-weight:600;margin-top:18px;height:40px}
.card .img{width:284px;height:194px;margin-top:0}
.card p{font-size:14px;line-height:20px;margin-top:15px}
.stars{margin-top:10px;display:flex;justify-content:center;gap:3px}
.price{font-size:24px;font-weight:700;margin-top:4px}

/* wholesale */
.wholesale{top:1870px;height:633px;background:var(--black)}
.w-box{position:absolute;left:150px;top:110px;width:436px;height:383px;background:var(--panel)}

/* testimonials */
.testimonials{top:2503px;height:522px;background:linear-gradient(180deg,#1a1612,#25201b 50%,#15120f)}
.quote{position:absolute;top:160px;width:248px;text-align:center}
.quote p{font-size:13.5px;line-height:24px;text-align:justify;text-align-last:center;color:var(--muted);margin-top:18px}
.quote .line{height:1px;background:#5a4c41;margin:16px 0 10px}
.quote h4{font-size:16px;font-weight:600}
.quote small{font-size:12px;display:block;margin-top:8px}

/* newsletter */
.newsletter{top:3025px;height:308px;background:var(--black)}
.field{position:absolute;left:300px;top:158px;width:598px;height:50px;border-radius:25px;background:#1a1714}

/* footer */
.footer{top:3333px;height:353px;background:var(--panel)}
.f-title{position:absolute;top:62px;font-size:20px;font-weight:700}
.f-text{position:absolute;font-size:13.5px;line-height:20px}
.icon-dot{position:absolute;width:34px;height:34px;border-radius:50%;background:var(--brown);display:flex;align-items:center;justify-content:center}
.links li{list-style:none;font-size:13.5px;height:24px}
</style>
</head>
<body>

<header class="nav">
  <a class="active" style="left:150px">HOME</a>
  <a style="left:238px">ABOUT US</a>
  <a style="left:340px">RETAIL COLLECTIONS</a>
  <div class="brand">
    <div class="brand-name">ORVANO GOODS</div>
    <div class="brand-sub">A DIVISION OF KRWZ HOSPITALITY</div>
    <div class="brand-tag">Purveyors of Luxury Lifestyle Accoutrements</div>
  </div>
  <a style="left:743px">WHOLESALE</a>
  <a style="left:860px">PARTNER</a>
  <a style="left:954px">CONTACT</a>
</header>

<section class="hero">
  <div class="abs" role="img" aria-label="Gentleman in a waistcoat relaxing in a dim leather cigar lounge" style="inset:0;background:radial-gradient(ellipse at 62% 28%,rgba(90,72,58,.55),rgba(0,0,0,0) 55%)"></div>
  <h1 class="hero-title">PURVEYORS OF LUXURY<br>LIFESTYLE ACCOUTREMENTS</h1>
  <div class="hero-sub">Curated for connoisseurs. Crafted for lounges.</div>
  <div class="btn" style="left:448px;top:410px;width:144px;height:43px">Shop Retail</div>
  <div class="btn" style="left:608px;top:410px;width:144px;height:43px">Trade Portal</div>
  <div class="circle-btn" style="left:558px;top:546px"><svg width="12" height="12" viewBox="0 0 12 12"><path d="M8 1L3 6l5 5" stroke="#000" stroke-width="2" fill="none"/></svg></div>
  <div class="circle-btn" style="left:606px;top:546px"><svg width="12" height="12" viewBox="0 0 12 12"><path d="M4 1l5 5-5 5" stroke="#000" stroke-width="2" fill="none"/></svg></div>
</section>

<section class="story">
  <svg class="abs" style="left:150px;top:75px" width="440" height="420"><ellipse cx="220" cy="210" rx="210" ry="210" fill="#6a5849"/></svg>
  <div class="photo" style="left:143px;top:94px;width:436px;height:384px;background:var(--black)">
    <div class="fill" role="img" aria-label="Row of hand-rolled cigars resting on a rustic wooden mold" style="background:linear-gradient(135deg,#4a3a2c,#7a5e42 45%,#2e241c)"></div>
  </div>
  <h2 class="heading abs" style="left:627px;top:92px">OUR STORY</h2>
  <div class="rule" style="left:627px;top:141px"></div>
  <p class="body-copy abs" style="left:627px;top:164px;width:428px">Lorem ipsum dolor sit amet, consectetur adipiscing elit, sed do eiusmod tempor incididunt ut labore et dolore magna aliqua. Ut enim ad minim veniam, quis nostrud exercitation ullamco laboris nisi ut aliquip ex ea commodo consequat. Duis aute irure dolor in reprehenderit in voluptate velit esse cillum dolore eu fugiat nulla pariatur. Excepteur sint occaecat cupidatat non proident, sunt in culpa qui officia deserunt mollit anim id est laborum. Lorem ipsum dolor sit amet, consectetur adipiscing elit, sed do eiusmod tempor incididunt ut labore et dolore magna aliqua. Ut enim ad minim veniam, quis nostrud exercitation ullamco laboris nisi ut aliquip ex ea commodo consequat.</p>
  <div class="btn" style="left:625px;top:436px;width:145px;height:42px">Learn More</div>
</section>

<section class="featured">
  <h2 class="heading abs" style="width:100%;text-align:center;top:72px">FEATURED COLLECTIONS</h2>
  <div class="rule" style="left:569px;top:124px"></div>
  <div class="circle-btn" style="left:54px;top:330px;width:40px;height:40px"><svg width="12" height="12" viewBox="0 0 12 12"><path d="M8 1L3 6l5 5" stroke="#000" stroke-width="2" fill="none"/></svg></div>
  <div class="circle-btn" style="left:1108px;top:330px;width:40px;height:40px"><svg width="12" height="12" viewBox="0 0 12 12"><path d="M4 1l5 5-5 5" stroke="#000" stroke-width="2" fill="none"/></svg></div>

  <div class="card" style="left:143px">
    <h3>Cigar Accessories</h3>
    <div class="img" role="img" aria-label="Silver lighter, cigar cutter and cigars on red leather" style="background:linear-gradient(135deg,#f2f2f2 0%,#c58a55 45%,#7a1a1a 100%)"></div>
    <p>Lorem ipsum dolor sit amet,<br>consectetur</p>
    <div class="stars"><svg width="88" height="14" viewBox="0 0 88 14" fill="var(--star)"><g id="s"><path d="M7 0l2 4.5 5 .5-3.8 3.3 1.2 4.9L7 10.7 2.6 13.2l1.2-4.9L0 5l5-.5z"/></g><use href="#s" x="18"/><use href="#s" x="36"/><use href="#s" x="54"/><use href="#s" x="72"/></svg></div>
    <div class="price">$25.00</div>
  </div>
  <div class="card" style="left:458px">
    <h3>Oils</h3>
    <div class="img" role="img" aria-label="Glass bottle of golden oil beside fresh herbs" style="background:linear-gradient(135deg,#4a4440,#8a6a30 50%,#2c2824);position:relative">
      <div class="btn" style="left:70px;top:78px;width:144px;height:38px;font-size:13px">Quick View</div>
    </div>
    <p>Lorem ipsum dolor sit amet,<br>consectetur</p>
    <div class="stars"><svg width="88" height="14" viewBox="0 0 88 14" fill="var(--star)"><use href="#s"/><use href="#s" x="18"/><use href="#s" x="36"/><use href="#s" x="54"/><use href="#s" x="72"/></svg></div>
    <div class="price">$25.00</div>
  </div>
  <div class="card" style="left:772px">
    <h3>Fragrances</h3>
    <div class="img" role="img" aria-label="Open black gift box with fragrance bottles" style="background:linear-gradient(135deg,#5a5a5a,#2b2b2b 55%,#6a6a6a)"></div>
    <p>Lorem ipsum dolor sit amet,<br>consectetur</p>
    <div class="stars"><svg width="88" height="14" viewBox="0 0 88 14" fill="var(--star)"><use href="#s"/><use href="#s" x="18"/><use href="#s" x="36"/><use href="#s" x="54"/><use href="#s" x="72"/></svg></div>
    <div class="price">$25.00</div>
  </div>
</section>

<section class="wholesale">
  <div class="w-box">
    <h2 class="heading abs" style="left:27px;top:20px">WHOLESALE PORTAL</h2>
    <div class="rule" style="left:27px;top:70px"></div>
    <p class="body-copy abs" style="left:32px;top:88px;width:367px">Lorem ipsum dolor sit amet, consectetur adipiscing elit, sed do eiusmod tempor incididunt ut labore et dolore magna aliqua. Ut enim ad minim veniam, quis nostrud exercitation ullamco laboris nisi ut aliquip ex ea commodo consequat. Duis aute irure dolor in reprehenderit in voluptate velit esse cillum dolore eu fugiat nulla pariatur. Excepteur sint occaecat cupidatat non proident, sunt in culpa qui officia deserunt mollit anim id est laborum. Lorem ipsum dolor sit amet</p>
    <div class="btn" style="left:29px;top:316px;width:208px;height:42px">View Our Special Events</div>
  </div>
  <div class="photo" style="left:591px;top:62px;width:475px;height:478px;background:var(--black)">
    <div class="fill" role="img" aria-label="Open wooden humidor filled with banded cigars" style="background:linear-gradient(135deg,#c9a57a,#8a5a34 50%,#3a2416)"></div>
  </div>
</section>

<section class="testimonials">
  <div class="abs" role="img" aria-label="Faded vintage photograph of people in a lounge" style="inset:0;background:radial-gradient(ellipse at 50% 40%,rgba(70,60,50,.35),rgba(0,0,0,0) 70%)"></div>
  <h2 class="heading abs" style="width:100%;text-align:center;top:78px">TESTIMONIALS</h2>
  <div class="rule" style="left:569px;top:130px"></div>
  <div class="circle-btn" style="left:52px;top:291px;width:40px;height:40px"><svg width="12" height="12" viewBox="0 0 12 12"><path d="M8 1L3 6l5 5" stroke="#000" stroke-width="2" fill="none"/></svg></div>
  <div class="circle-btn" style="left:1108px;top:291px;width:40px;height:40px"><svg width="12" height="12" viewBox="0 0 12 12"><path d="M4 1l5 5-5 5" stroke="#000" stroke-width="2" fill="none"/></svg></div>

  <div class="quote" style="left:143px">
    <svg width="34" height="28" viewBox="0 0 34 28" fill="#fff"><path d="M0 28V16C0 7 4 2 12 0l2 4c-4 2-6 5-6 9h6v15zM19 28V16c0-9 4-14 12-16l2 4c-4 2-6 5-6 9h6v15z"/></svg>
    <p>Lorem ipsum dolor sit amet, consectetur adipiscing elit, sed do eiusmod tempor incididunt ut labore et dolore magna aliqua. Ut enim ad minim veniam, quis nostrud exercitation ullamco laboris nisi ut aliquip ex ea commodo consequat.</p>
    <div class="line"></div><h4>John Doe</h4><small>Company name</small>
  </div>
  <div class="quote" style="left:474px">
    <svg width="34" height="28" viewBox="0 0 34 28" fill="#fff"><path d="M0 28V16C0 7 4 2 12 0l2 4c-4 2-6 5-6 9h6v15zM19 28V16c0-9 4-14 12-16l2 4c-4 2-6 5-6 9h6v15z"/></svg>
    <p>Lorem ipsum dolor sit amet, consectetur adipiscing elit, sed do eiusmod tempor incididunt ut labore et dolore magna aliqua. Ut enim ad minim veniam, quis nostrud exercitation ullamco laboris nisi ut aliquip ex ea commodo consequat.</p>
    <div class="line"></div><h4>John Doe</h4><small>Company name</small>
  </div>
  <div class="quote" style="left:805px">
    <svg width="34" height="28" viewBox="0 0 34 28" fill="#fff"><path d="M0 28V16C0 7 4 2 12 0l2 4c-4 2-6 5-6 9h6v15zM19 28V16c0-9 4-14 12-16l2 4c-4 2-6 5-6 9h6v15z"/></svg>
    <p>Lorem ipsum dolor sit amet, consectetur adipiscing elit, sed do eiusmod tempor incididunt ut labore et dolore magna aliqua. Ut enim ad minim veniam, quis nostrud exercitation ullamco laboris nisi ut aliquip ex ea commodo consequat.</p>
    <div class="line"></div><h4>John Doe</h4><small>Company name</small>
  </div>
</section>

<section class="newsletter">
  <h2 class="heading abs" style="width:100%;text-align:center;top:76px">SUBSCRIBE TO OUR NEWSLETTER</h2>
  <div class="rule" style="left:569px;top:126px"></div>
  <div class="field">
    <span class="abs" style="left:29px;top:16px;font-size:14px">Email address</span>
    <div class="btn" style="left:452px;top:3px;width:144px;height:44px">Subscribe</div>
  </div>
</section>

<footer class="footer">
  <div class="f-title" style="left:143px">LOCATION</div>
  <div class="icon-dot" style="left:143px;top:114px"><svg width="12" height="14" viewBox="0 0 12 14"><path d="M6 0a5 5 0 0 0-5 5c0 4 5 9 5 9s5-5 5-9a5 5 0 0 0-5-5zm0 7a2 2 0 1 1 0-4 2 2 0 0 1 0 4z" fill="#fff"/></svg></div>
  <div class="f-text" style="left:194px;top:112px">Lorem ipsum dolor<br>sit amet, consectetur</div>
  <div class="icon-dot" style="left:143px;top:172px"><svg width="13" height="13" viewBox="0 0 13 13"><path d="M3 0l2 3-1.5 1.5c.8 1.8 2.2 3.2 4 4L9 7l3 2-1 3C6 12 1 7 0 2z" fill="#fff"/></svg></div>
  <div class="f-text" style="left:194px;top:180px">+1 888 888 8888</div>

  <div class="f-title" style="left:391px">OPENING HOURS</div>
  <div class="icon-dot" style="left:391px;top:114px"><svg width="14" height="14" viewBox="0 0 14 14"><circle cx="7" cy="7" r="6" stroke="#fff" stroke-width="1.6" fill="none"/><path d="M7 4v3.5h2.5" stroke="#fff" stroke-width="1.6" fill="none"/></svg></div>
  <div class="f-text" style="left:442px;top:112px">Monday - Tuesday:<br>Closed</div>
  <div class="f-text" style="left:442px;top:172px">Wednesday - Sunday:<br>11:30 am - 9:00 pm</div>

  <div class="f-title" style="left:687px">LINKS</div>
  <ul class="links abs" style="left:687px;top:110px">
    <li>»&nbsp;&nbsp;&nbsp;Home</li><li>»&nbsp;&nbsp;&nbsp;Our Story</li><li>»&nbsp;&nbsp;&nbsp;Products</li><li>»&nbsp;&nbsp;&nbsp;Reviews</li><li>»&nbsp;&nbsp;&nbsp;Contact</li>
  </ul>

  <div class="abs" style="left:828px;top:100px;width:240px;text-align:center">
    <div style="font-family:'Cinzel',serif;font-size:24px;font-weight:500">ORVANO GOODS</div>
    <div style="font-family:'Cinzel',serif;font-size:8px;font-weight:500;letter-spacing:1.5px;margin-top:2px">A DIVISION OF KRWZ HOSPITALITY</div>
    <div style="font-family:'Cinzel',serif;font-size:11px;font-weight:500;margin-top:8px">Purveyors of Luxury Lifestyle Accoutrements</div>
  </div>

  <div class="abs" style="left:143px;top:259px;width:912px;height:1px;background:#3a332d"></div>
  <div class="abs" style="width:100%;text-align:center;top:295px;font-size:14px">© Copyrights 2026 | All Rights Reserved</div>
</footer>

</body>
</html>
```